New website for out outstanding veterinary training center

We already have a beautiful logo with nice colors and we are now looking for a breathtaking modern website to present our training center and future corses held there. A section to book open courses should also be available.

We are planing the realize the website with Wordpress.
The following pages should be available:
- Startpage / Overview
- Page to present the different rooms and seating option
- Page where the rooms can be booked
- Page where recommended accommodation are presented
- Page to present and book corses
- contact page
- Impressum

Target Market(s)

European Union

Industry/Entity Type

Education, Veterinary medicine

Number of Pages Required

5+ page

Font styles to use
Sans Serif

Colors
00AB8E
00BBA5
67D7C9
C6EFE9
E9F9F6

Requirements
Must have
• The website must be clear and easy to read. The colors form the logos should be used for the design.
Should not have
• To playful design. The page is not for a veterinary practice. we are a training center for veterinarians!

```html
<!DOCTYPE html>
<html lang="en">
<head>
<meta charset="utf-8">
<title>Vetaris Training Center</title>
<link href="https://fonts.googleapis.com/css2?family=Lato:wght@400;700;900&display=swap" rel="stylesheet">
<style>
:root{
  --teal:#00ab8e;
  --teal-2:#00bba5;
  --teal-dark:#1a7f73;
  --mint:#b5eae2;
  --mint-soft:#e3f6f3;
  --mint-top:#e9f9f6;
  --plum:#45323e;
  --text:#4a3d45;
  --white:#ffffff;
}
*{margin:0;padding:0;box-sizing:border-box}
html,body{width:1200px;height:5080px;overflow:hidden;background:var(--white)}
body{position:relative;font-family:'Lato',sans-serif;color:var(--text)}
.abs{position:absolute}
.btn{position:absolute;display:flex;align-items:center;justify-content:center;background:var(--teal);color:var(--white);font-weight:700;font-size:17px;border-radius:26px;text-decoration:none}
.section-title{position:absolute;left:0;width:1200px;text-align:center;font-weight:700;font-size:42px;color:var(--plum)}
.rule{position:absolute;height:5px;width:72px;background:var(--teal-dark);border-radius:2px}
.rule.center{left:564px}

/* top bar */
.topbar{left:0;top:0;width:1200px;height:58px;background:var(--mint-top)}
.social{position:absolute;top:19px;display:flex;gap:12px}
.social span{width:20px;height:20px;border-radius:50%;background:var(--plum)}
.brand{position:absolute;left:75px;top:112px;display:flex;align-items:center;gap:10px}
.brand .dot{width:40px;height:40px;border-radius:50%;background:var(--teal-dark)}
.brand .name{font-weight:900;font-size:24px;color:var(--plum);line-height:1}
.nav{position:absolute;top:102px;font-size:16px;font-weight:700;color:var(--plum)}

/* hero */
.hero{left:0;top:168px;width:1200px;height:702px;background:linear-gradient(120deg,#c9c2b8 0%,#9fb3ad 35%,#5f8f86 60%,#d6d0c6 100%)}
.hero-title{position:absolute;left:0;top:345px;width:1200px;text-align:center;color:var(--white);font-weight:700;font-size:70px;line-height:74px;text-shadow:0 2px 6px rgba(0,0,0,.25)}
.dots{position:absolute;top:780px;left:560px;display:flex;gap:10px}
.dots span{width:11px;height:11px;border-radius:50%;background:rgba(255,255,255,.5)}
.dots span:first-child{background:var(--white)}

/* overview */
.overview-title{left:75px;top:980px;font-size:40px;font-weight:700;color:var(--plum)}
.body-copy{font-size:15px;line-height:31.5px;color:var(--text)}
.emblem{left:661px;top:922px;width:464px;height:464px;border-radius:50%;background:var(--teal-dark);display:flex;align-items:center;justify-content:center;color:var(--white);font-weight:900;font-size:40px}

/* bands */
.band{left:0;width:1200px;background:var(--mint)}
.card{position:absolute;width:330px;text-align:center}
.card .photo{width:330px;height:202px;border-radius:4px}
.card h3{margin-top:20px;font-size:22px;font-weight:700;color:var(--plum)}
.card p{margin-top:8px;font-size:15px;line-height:27.5px;padding:0 12px}
.card .btn{position:relative;margin:14px auto 0;width:178px;height:52px}

/* why choose */
.why{left:0;top:3385px;width:1200px;height:484px;background:linear-gradient(135deg,#1e7f74 0%,#2f6f68 50%,#1a7f73 100%)}
.why h2{position:absolute;top:110px;width:1200px;text-align:center;color:var(--white);font-size:46px;font-weight:700;letter-spacing:1px}
.why-item{position:absolute;top:211px;width:220px;text-align:center;color:var(--white);font-size:22px;font-weight:700}
.why-item .circle{width:124px;height:124px;margin:0 auto 22px;border-radius:50%;background:var(--white);display:flex;align-items:center;justify-content:center}

/* testimonials */
.quote-card{position:absolute;top:4013px;width:330px;height:373px;background:var(--mint-soft)}
.quote-card .mark{position:absolute;left:2px;top:-2px;font-size:52px;font-weight:900;color:var(--plum);line-height:1}
.quote-card p{position:absolute;left:43px;top:53px;width:232px;font-size:14.5px;line-height:25px;color:var(--text)}
.author{position:absolute;left:45px;top:306px;display:flex;align-items:center;gap:12px;font-size:11px;line-height:15px;color:var(--plum)}
.author .avatar{width:40px;height:40px;border-radius:50%;background:#b9c3c8}
.arrow{position:absolute;top:4190px}

/* footer */
.footer{left:0;top:4453px;width:1200px;height:399px;background:var(--plum);color:var(--white)}
.footer h4{position:absolute;top:68px;color:var(--teal-2);font-size:23px;font-weight:700}
.footer ul{position:absolute;top:112px;list-style:none;font-size:15px;line-height:33.5px}
.footer .info{position:absolute;font-size:15px;line-height:28px}
.foot-brand{position:absolute;left:75px;top:150px;width:230px;text-align:center}
.foot-brand .dot{width:110px;height:110px;margin:0 auto 16px;border-radius:50%;background:var(--white)}
.foot-brand .name{font-weight:900;font-size:30px;color:var(--white)}
.input{position:absolute;left:884px;top:172px;width:241px;height:44px;border-radius:22px;background:var(--white);color:var(--plum);font-size:14px;padding:13px 18px}
.foot-social{position:absolute;left:604px;top:255px;display:flex;gap:16px}
.foot-social span{width:18px;height:18px;border-radius:50%;background:var(--teal-2)}
</style>
</head>
<body>

<header>
  <div class="abs topbar">
    <div class="social" style="left:775px"><span></span><span></span><span></span><span></span><span></span></div>
    <a class="btn" style="left:981px;top:8px;width:144px;height:40px;font-size:14px">Book Course</a>
  </div>
  <div class="brand"><span class="dot"></span><span class="name">Vetaris</span></div>
  <nav>
    <span class="nav" style="left:347px">Home</span>
    <span class="nav" style="left:428px">About Us</span>
    <span class="nav" style="left:537px">Rooms</span>
    <span class="nav" style="left:626px">Book Course</span>
    <span class="nav" style="left:760px">Accommodation</span>
    <span class="nav" style="left:922px">Impressum</span>
    <span class="nav" style="left:1044px">Contact Us</span>
  </nav>
</header>

<section class="abs hero" role="img" aria-label="Photo of two veterinarians examining a small white dog on a clinic table">
</section>
<div class="hero-title">Vetaris<br>Training Center</div>
<a class="btn" style="left:509px;top:537px;width:178px;height:50px">Book Course</a>
<div class="dots"><span></span><span></span><span></span><span></span></div>
<svg class="abs" style="left:0;top:820px" width="1200" height="52" viewBox="0 0 1200 52">
  <path d="M0,40 C300,22 450,8 600,8 C750,8 900,22 1200,40 L1200,52 L0,52Z" fill="#fff"/>
</svg>

<section>
  <h2 class="abs overview-title">Company Overview</h2>
  <p class="abs body-copy" style="left:75px;top:1067px;width:530px">Sed ut perspiciatis unde omnis iste natus error sit voluptatem accusantium doloremque laudantium, totam rem aperiam, eaque ipsa quae ab illo inventore veritatis et quasi architecto beatae vitae dicta sunt explicabo. Nemo enim ipsam voluptatem quia voluptas sit aspernatur aut odit aut fugit, sed quia consequuntur magni dolores eos qui ratione voluptatem sequi nesciunt.</p>
  <a class="btn" style="left:75px;top:1285px;width:178px;height:52px">Read More</a>
  <div class="abs emblem">Vetaris</div>
</section>

<section>
  <div class="abs band" style="top:1461px;height:681px"></div>
  <svg class="abs" style="left:0;top:2110px" width="1200" height="40" viewBox="0 0 1200 40">
    <path d="M0,32 C300,20 450,12 600,12 C750,12 900,20 1200,32 L1200,40 L0,40Z" fill="#fff"/>
  </svg>
  <h2 class="section-title" style="top:1517px">Feature Courses</h2>
  <div class="rule center" style="top:1587px"></div>
  <div class="card" style="left:75px;top:1644px">
    <div class="photo" role="img" aria-label="Photo of a student studying beside an animal skeleton" style="background:linear-gradient(135deg,#d9d2c8,#a89684)"></div>
    <h3>Course Heading</h3>
    <p>Sed ut perspiciatis unde omnis iste natus error sit voluptatem accusantium doloremque quaerat.</p>
    <a class="btn">Book Course</a>
  </div>
  <div class="card" style="left:436px;top:1644px">
    <div class="photo" role="img" aria-label="Photo of a veterinarian with a stethoscope examining a dog" style="background:linear-gradient(135deg,#eef0ee,#b78455)"></div>
    <h3>Course Heading</h3>
    <p>Sed ut perspiciatis unde omnis iste natus error sit voluptatem accusantium doloremque quaerat.</p>
    <a class="btn">Book Course</a>
  </div>
  <div class="card" style="left:796px;top:1644px">
    <div class="photo" role="img" aria-label="Photo of a lecturer presenting at a whiteboard to students" style="background:linear-gradient(135deg,#c9ccc4,#9aa3a0)"></div>
    <h3>Course Heading</h3>
    <p>Sed ut perspiciatis unde omnis iste natus error sit voluptatem accusantium doloremque quaerat.</p>
    <a class="btn">Book Course</a>
  </div>
</section>

<section>
  <h2 class="section-title" style="top:2226px">Rooms &amp; Seating Option</h2>
  <div class="rule center" style="top:2296px"></div>
  <div class="card" style="left:75px;top:2355px">
    <div class="photo" role="img" aria-label="Photo of a veterinarian holding a puppy in a bright room" style="background:linear-gradient(135deg,#e4e6e4,#8b7e72)"></div>
    <h3>Room Heading</h3>
    <p>Sed ut perspiciatis unde omnis iste natus error sit voluptatem accusantium doloremque quaerat.</p>
    <a class="btn">More Info</a>
  </div>
  <div class="card" style="left:436px;top:2355px">
    <div class="photo" role="img" aria-label="Photo of a seminar room with rows of blue chairs" style="background:linear-gradient(180deg,#e6eaee,#7f98b8)"></div>
    <h3>Room Heading</h3>
    <p>Sed ut perspiciatis unde omnis iste natus error sit voluptatem accusantium doloremque quaerat.</p>
    <a class="btn">More Info</a>
  </div>
  <div class="card" style="left:796px;top:2355px">
    <div class="photo" role="img" aria-label="Photo of a classroom with desks and a projector screen" style="background:linear-gradient(180deg,#dfe2e4,#8c8478)"></div>
    <h3>Room Heading</h3>
    <p>Sed ut perspiciatis unde omnis iste natus error sit voluptatem accusantium doloremque quaerat.</p>
    <a class="btn">More Info</a>
  </div>
</section>

<section>
  <svg class="abs" style="left:0;top:2826px" width="1200" height="560" viewBox="0 0 1200 560">
    <path d="M0,34 C300,30 500,18 600,2 C700,18 900,30 1200,34 L1200,560 L0,560Z" fill="#b5eae2"/>
  </svg>
  <div class="abs" role="img" aria-label="Photo of two travellers with backpacks in a hotel room" style="left:75px;top:2959px;width:511px;height:355px;background:linear-gradient(135deg,#b88a6e,#e6dccf 60%,#c9b6c6)"></div>
  <h2 class="abs" style="left:616px;top:2952px;font-size:42px;font-weight:700;color:var(--plum)">Accommodation</h2>
  <div class="rule" style="left:616px;top:3022px"></div>
  <p class="abs body-copy" style="left:616px;top:3041px;width:520px">Sed ut perspiciatis unde omnis iste natus error sit voluptatem accusantium doloremque laudantium, totam rem aperiam, eaque ipsa quae ab illo inventore veritatis et quasi architecto beatae vitae dicta sunt explicabo. Nemo enim ipsam voluptatem quia voluptas sit aspernatur aut odit aut fugit, sed quia consequuntur magni dolores eos qui ratione voluptatem sequi nesciunt.</p>
  <a class="btn" style="left:616px;top:3259px;width:178px;height:52px">Read More</a>
</section>

<section class="abs why" role="img" aria-label="Dark teal background photo of a dog and cat resting under a blanket">
  <h2>WHY CHOOSE US</h2>
  <div class="why-item" style="left:95px">
    <div class="circle"><svg width="56" height="56" viewBox="0 0 56 56"><circle cx="28" cy="32" r="14" fill="#1a7f73"/><circle cx="12" cy="20" r="6" fill="#1a7f73"/><circle cx="44" cy="20" r="6" fill="#1a7f73"/><circle cx="21" cy="10" r="6" fill="#1a7f73"/><circle cx="35" cy="10" r="6" fill="#1a7f73"/><path d="M28 25v14M21 32h14" stroke="#fff" stroke-width="3"/></svg></div>Lorem ipsum</div>
  <div class="why-item" style="left:358px">
    <div class="circle"><svg width="56" height="56" viewBox="0 0 56 56"><rect x="8" y="18" width="40" height="32" fill="#1a7f73"/><rect x="14" y="8" width="28" height="8" fill="#1a7f73"/><rect x="15" y="26" width="10" height="10" fill="#fff"/><rect x="31" y="26" width="10" height="10" fill="#fff"/></svg></div>Lorem ipsum</div>
  <div class="why-item" style="left:622px">
    <div class="circle"><svg width="56" height="56" viewBox="0 0 56 56"><path d="M14 8v16a10 10 0 0 0 20 0V8" fill="none" stroke="#1a7f73" stroke-width="4"/><path d="M24 34v6a8 8 0 0 0 16 0v-6" fill="none" stroke="#1a7f73" stroke-width="4"/><circle cx="40" cy="30" r="6" fill="#1a7f73"/></svg></div>Lorem ipsum</div>
  <div class="why-item" style="left:885px">
    <div class="circle"><svg width="56" height="56" viewBox="0 0 56 56"><rect x="14" y="6" width="28" height="44" rx="3" fill="#1a7f73"/><rect x="20" y="13" width="16" height="4" fill="#fff"/><rect x="20" y="21" width="16" height="4" fill="#fff"/><circle cx="28" cy="38" r="5" fill="#fff"/></svg></div>Lorem ipsum</div>
</section>

<section>
  <h2 class="section-title" style="top:3905px">Testimonials</h2>
  <div class="rule center" style="top:3976px"></div>
  <svg class="arrow" style="left:44px" width="18" height="30" viewBox="0 0 18 30"><path d="M15 3L4 15l11 12" fill="none" stroke="#7a6f76" stroke-width="2"/></svg>
  <svg class="arrow" style="left:1140px" width="18" height="30" viewBox="0 0 18 30"><path d="M3 3l11 12L3 27" fill="none" stroke="#7a6f76" stroke-width="2"/></svg>
  <div class="quote-card" style="left:75px"><span class="mark">“</span>
    <p>But I must explain to you how all this mistaken idea of denou ncing pleasure and praising pain was born and I will give you a complete account of the sys tem, and expound the actual teachings of the great explorer of the truth.</p>
    <div class="author"><span class="avatar"></span><span>RICHARD<br>England</span></div></div>
  <div class="quote-card" style="left:436px"><span class="mark">“</span>
    <p>But I must explain to you how all this mistaken idea of denou ncing pleasure and praising pain was born and I will give you a complete account of the sys tem, and expound the actual teachings of the great explorer of the truth.</p>
    <div class="author"><span class="avatar"></span><span>RICHARD<br>England</span></div></div>
  <div class="quote-card" style="left:796px"><span class="mark">“</span>
    <p>But I must explain to you how all this mistaken idea of denou ncing pleasure and praising pain was born and I will give you a complete account of the system, and expound the actual teachings of the great explorer of the truth,</p>
    <div class="author"><span class="avatar"></span><span>RICHARD<br>England</span></div></div>
</section>

<footer class="abs footer">
  <div class="foot-brand"><div class="dot"></div><div class="name">Vetaris</div></div>
  <h4 style="left:365px">Site Map</h4>
  <ul style="left:365px"><li>Home</li><li>About Us</li><li>Rooms</li><li>Book Course</li><li>Accommodation</li><li>Impressum</li><li>Contact Us</li></ul>
  <h4 style="left:604px">Contact Us</h4>
  <div class="info" style="left:604px;top:110px;width:200px">Neque porro quisquam est,qui dolorem</div>
  <div class="info" style="left:604px;top:171px">1-800-555-0147</div>
  <div class="info" style="left:604px;top:205px">hello@vetaris-training.eu</div>
  <div class="foot-social"><span></span><span></span><span></span><span></span><span></span></div>
  <h4 style="left:884px">Email Subscribe</h4>
  <div class="info" style="left:887px;top:114px;width:230px">Neque porro quisquam est, qui dolorem</div>
  <div class="input">Email Address</div>
  <a class="btn" style="left:884px;top:231px;width:241px;height:46px;font-size:19px">Subscribe</a>
</footer>

</body>
</html>
```